Brookvale Building Company - advertisement poster

I am looking to print some canvas signs to advertise my general contracting company, Brookvale Building Company. The sign will measure 6' long x 3' high so the size should match that ratio. I already have a logo icon, which is the Letter 'B' and some trees that I would like to incorporate, see attached. I would also like the to have the following information listed:
1) phone number: 831-555-0172
2) email: brookvalebuildingcompany@mailnest.example
3) website: brookvalebuildingcompany.example
4) Lic#4826130
5) I want to use this text: "BUILD WITH THE B-CREW!"

The ad should be relatively simple and clean. Black and Green are my company colors. I am open to creative ideas!

Target Market(s)

People looking to renovate their homes

Industry/Entity Type

Construction

Colors
59FF00
82FF00
B8FF75
E3FFCB
F4FFEA

Requirements
Must have
• Must have my company logo
Should not have
• No photos or complex graphics

```html
<!DOCTYPE html>
<html lang="en">
<head>
<meta charset="utf-8">
<title>Brookvale Building Company – Canvas Sign</title>
<link rel="stylesheet" href="https://fonts.googleapis.com/css2?family=Bebas+Neue&family=Montserrat:wght@500&family=Orbitron:wght@400;700&display=swap">
<style>
  :root {
    --backdrop: #797979;
    --black: #000000;
    --green: #72b84a;
    --green-dark: #5d9a3b;
    --white: #ffffff;
  }
  * { margin: 0; padding: 0; box-sizing: border-box; }
  html, body {
    width: 1200px;
    height: 904px;
    overflow: hidden;
    background: var(--backdrop);
  }
  .sign {
    position: absolute;
    left: 131px;
    top: 218px;
    width: 937px;
    height: 469px;
    background: var(--black);
    overflow: hidden;
  }
  .sign__shapes {
    position: absolute;
    inset: 0;
    width: 937px;
    height: 469px;
  }

  /* Logo lockup */
  .logo-mark {
    position: absolute;
    left: 428px;
    top: 40px;
    width: 80px;
    height: 80px;
    background: var(--green);
  }
  .est {
    position: absolute;
    top: 92px;
    width: 56px;
    height: 20px;
    border-top: 1px solid var(--green);
    border-bottom: 1px solid var(--green);
    color: var(--white);
    font-family: "Orbitron", sans-serif;
    font-weight: 400;
    font-size: 10px;
    line-height: 18px;
    letter-spacing: 3px;
    text-indent: 3px;
    text-align: center;
  }
  .est--label { left: 312px; }
  .est--year  { left: 568px; }

  .brand__name {
    position: absolute;
    left: 0;
    right: 0;
    top: 138px;
    text-align: center;
    color: var(--white);
    font-family: "Orbitron", sans-serif;
    font-weight: 700;
    font-size: 40px;
    line-height: 40px;
    letter-spacing: 1px;
  }
  .brand__tagline {
    position: absolute;
    left: 0;
    right: 0;
    top: 182px;
    text-align: center;
    color: var(--green);
    font-family: "Orbitron", sans-serif;
    font-weight: 400;
    font-size: 15px;
    line-height: 18px;
    letter-spacing: 8px;
    text-indent: 8px;
  }

  .headline {
    position: absolute;
    left: 0;
    right: 0;
    top: 234px;
    text-align: center;
    white-space: nowrap;
    color: var(--white);
    font-family: "Bebas Neue", sans-serif;
    font-weight: 400;
    font-size: 110px;
    line-height: 1;
    letter-spacing: 2px;
  }

  .contact-bar {
    position: absolute;
    left: 0;
    top: 350px;
    width: 937px;
    height: 100px;
    background: var(--green);
    color: var(--black);
  }
  .contact-bar__primary {
    position: absolute;
    left: 30px;
    top: 8px;
    width: 300px;
    text-align: center;
  }
  .phone {
    display: block;
    font-family: "Bebas Neue", sans-serif;
    font-size: 60px;
    line-height: 1;
    letter-spacing: 0.5px;
  }
  .licence {
    display: block;
    margin-top: -2px;
    font-family: "Montserrat", sans-serif;
    font-weight: 500;
    font-size: 25px;
    line-height: 1;
  }
  .contact-bar__divider {
    position: absolute;
    left: 345px;
    top: 14px;
    width: 3px;
    height: 73px;
    background: var(--green-dark);
  }
  .contact-list {
    position: absolute;
    left: 369px;
    top: 16px;
    list-style: none;
  }
  .contact-list__item {
    display: flex;
    align-items: center;
    height: 34px;
    margin-bottom: 2px;
    font-family: "Montserrat", sans-serif;
    font-weight: 500;
    font-size: 20.5px;
    white-space: nowrap;
  }
  .contact-list__icon {
    width: 31px;
    height: 31px;
    margin-right: 12px;
    flex: none;
  }
</style>
</head>
<body>
  <main class="sign">
    <svg class="sign__shapes" viewBox="0 0 1728 864" preserveAspectRatio="none" aria-hidden="true">
      <polygon points="0,0 240,0 0,391" fill="var(--green)"/>
      <polygon points="276,0 361,0 210,252 123,252" fill="var(--white)"/>
      <polygon points="396,0 428,0 331,160 299,160" fill="var(--green)"/>
      <polygon points="1728,0 1488,0 1728,391" fill="var(--green)"/>
      <polygon points="1368,0 1452,0 1604,252 1520,252" fill="var(--white)"/>
      <polygon points="1300,0 1333,0 1429,160 1398,160" fill="var(--green)"/>
    </svg>

    <header class="brand">
      <div class="logo-mark" role="img" aria-label="Company logo mark"></div>
      <span class="est est--label">ESTD</span>
      <span class="est est--year">2020</span>
      <span class="brand__name">BROOKVALE</span>
      <span class="brand__tagline">BUILDING COMPANY</span>
    </header>

    <h1 class="headline">BUILD WITH THE B-CREW!</h1>

    <section class="contact-bar">
      <div class="contact-bar__primary">
        <span class="phone">831-555-0172</span>
        <span class="licence">Lic#4826130</span>
      </div>
      <div class="contact-bar__divider"></div>
      <ul class="contact-list">
        <li class="contact-list__item">
          <svg class="contact-list__icon" viewBox="0 0 32 32" aria-hidden="true">
            <circle cx="16" cy="16" r="14.5" fill="none" stroke="var(--black)" stroke-width="2.2"/>
            <circle cx="16" cy="16" r="9" fill="none" stroke="var(--black)" stroke-width="1.6"/>
            <ellipse cx="16" cy="16" rx="4" ry="9" fill="none" stroke="var(--black)" stroke-width="1.6"/>
            <line x1="7" y1="16" x2="25" y2="16" stroke="var(--black)" stroke-width="1.6"/>
            <line x1="8.5" y1="11.5" x2="23.5" y2="11.5" stroke="var(--black)" stroke-width="1.4"/>
            <line x1="8.5" y1="20.5" x2="23.5" y2="20.5" stroke="var(--black)" stroke-width="1.4"/>
          </svg>
          www.brookvalebuildingcompany.example
        </li>
        <li class="contact-list__item">
          <svg class="contact-list__icon" viewBox="0 0 32 32" aria-hidden="true">
            <circle cx="16" cy="16" r="14.5" fill="none" stroke="var(--black)" stroke-width="2.2"/>
            <rect x="8" y="10.5" width="16" height="11" fill="none" stroke="var(--black)" stroke-width="1.8"/>
            <polyline points="8,10.5 16,17 24,10.5" fill="none" stroke="var(--black)" stroke-width="1.8"/>
          </svg>
          brookvalebuildingcompany@mailnest.example
        </li>
      </ul>
    </section>
  </main>
</body>
</html>
```